Flyer for the Lumen 2025 Conference

I am looking to produce a flyer for our upcoming conference, Lumen 2025. This is an annual conference that we plan to publicize on social media. The ideal designer will create a flyer that is eye-catching and effectively communicates the key information. Please see attached our logo, speaker photo, and flyer content.

Target Market(s)

All demographics

Industry/Entity Type

Christian

Font styles to use
Sans Serif

Requirements
Should not have
• Cross, church

```html
<!DOCTYPE html>
<html lang="en">
<head>
<meta charset="utf-8">
<title>Lumen 2025 Conference – The Voice of the Lord</title>
<link rel="stylesheet" href="https://fonts.googleapis.com/css2?family=Bebas+Neue&family=Cinzel:wght@500;600&family=Montserrat:wght@500;600;700;800&display=swap">
<style>
  :root {
    --navy: #021a2e;
    --navy-deep: #01131f;
    --orange: #f7931e;
    --orange-bar: #e27f0e;
    --blue: #0066b3;
    --blue-panel: #005a9c;
    --blue-line: #1b5fa3;
    --white: #f7f8fa;
    --paper: #ffffff;
    --phone-screen: #eceff1;
    --phone-body: #1a1d21;
  }
  * { box-sizing: border-box; margin: 0; padding: 0; }
  html, body {
    width: 869px; height: 1200px; overflow: hidden;
    background: var(--paper);
    font-family: "Montserrat", sans-serif;
  }
  .flyer {
    position: absolute; left: 107px; top: 109px;
    width: 656px; height: 983px;
    background: var(--navy);
    overflow: hidden;
  }
  .flyer-art { position: absolute; inset: 0; }
  .speaker-photo {
    position: absolute; left: 0; top: 447px; width: 370px; height: 469px;
    background: radial-gradient(ellipse at 45% 55%, #1f6fc4 0%, #0d4a8e 45%, rgba(2,26,46,0) 80%);
  }
  .brand {
    position: absolute; top: 38px; left: 0; width: 100%;
    text-align: center; color: var(--white);
    font-family: "Cinzel", serif; font-weight: 500; font-size: 34px; letter-spacing: 1px;
  }
  .edition {
    position: absolute; top: 89px; width: 100%; text-align: center;
    color: var(--orange); font-weight: 600; font-size: 20px; letter-spacing: .5px;
  }
  .subtitle {
    position: absolute; top: 113px; width: 100%; text-align: center;
    color: var(--white); font-family: "Cinzel", serif; font-weight: 500; font-size: 28px; letter-spacing: 1px;
  }
  .dates { position: absolute; top: 456px; left: 242px; display: flex; gap: 11px; }
  .date-card {
    width: 127px; height: 178px; border: 1.5px solid var(--blue-line);
    text-align: center; color: var(--white); font-family: "Bebas Neue", sans-serif;
    padding-top: 8px; display: flex; flex-direction: column; align-items: center;
  }
  .date-month { font-size: 33px; line-height: 30px; }
  .date-day { font-size: 76px; line-height: 60px; margin-top: 4px; }
  .date-weekday { font-size: 48px; line-height: 44px; margin-top: 2px; height: 44px; }
  .date-weekday.long { font-size: 38px; }
  .date-time {
    margin-top: 6px; background: var(--orange); color: var(--navy);
    font-size: 20px; line-height: 23px; width: 108px; height: 23px;
  }
  .location {
    position: absolute; left: 338px; top: 652px; width: 271px; height: 106px;
    background: var(--blue-panel); text-align: center; color: var(--white);
  }
  .location-title {
    font-family: "Cinzel", serif; font-weight: 600; color: var(--orange);
    font-size: 19px; margin-top: 10px; letter-spacing: .5px;
  }
  .location-address { font-size: 11px; font-weight: 600; line-height: 17px; margin-top: 5px; }
  .app-promo {
    position: absolute; left: 413px; top: 772px; width: 128px; height: 150px;
    background: var(--phone-body); border-radius: 16px 16px 0 0; padding: 5px 5px 0;
  }
  .app-screen {
    width: 100%; height: 100%; background: var(--phone-screen); border-radius: 12px 12px 0 0;
    text-align: center; color: var(--navy-deep); padding-top: 34px;
  }
  .app-brand { font-family: "Cinzel", serif; font-weight: 500; font-size: 20px; color: var(--navy); }
  .app-call { font-size: 9px; font-weight: 700; margin-top: 8px; line-height: 10px; }
  .app-name { font-size: 14px; font-weight: 800; line-height: 15px; }
  .app-note { font-size: 5.5px; font-weight: 500; margin-top: 2px; }
  .store-badges { display: flex; justify-content: center; gap: 3px; margin-top: 8px; }
  .store-badge { width: 51px; height: 15px; background: var(--navy-deep); border-radius: 2px; }
  .speaker {
    position: absolute; left: 25px; top: 832px; color: var(--white);
  }
  .speaker-label { color: var(--orange); font-size: 20px; font-weight: 500; letter-spacing: .5px; line-height: 22px; }
  .speaker-name { font-size: 20px; font-weight: 500; line-height: 26px; }
  .contact-bar {
    position: absolute; left: 0; bottom: 0; width: 100%; height: 67px;
    background: var(--orange-bar); display: flex; align-items: center; color: var(--white);
  }
  .contact-item { display: flex; align-items: center; position: absolute; }
  .contact-item svg { width: 14px; height: 14px; }
  .divider { width: 1px; height: 22px; background: var(--white); margin: 0 8px; }
  .contact-phone { left: 30px; font-size: 25px; font-weight: 500; }
  .contact-mail { left: 262px; font-size: 15px; font-weight: 500; }
  .contact-web { left: 483px; font-size: 15px; font-weight: 500; }
</style>
</head>
<body>
<main class="flyer">
  <svg class="flyer-art" width="656" height="983" viewBox="0 0 656 983">
    <defs>
      <linearGradient id="beam" x1="0" y1="0" x2="1" y2="1">
        <stop offset="0" stop-color="#0a6fc2"/>
        <stop offset="1" stop-color="#0458a0"/>
      </linearGradient>
    </defs>
    <polygon class="light-beam" points="0,0 20,0 152,441 0,470" fill="url(#beam)"/>
  </svg>

  <div class="speaker-photo" role="img" aria-label="Photo of the speaker, seated, wearing a blue suit and glasses"></div>

  <svg class="flyer-art" width="656" height="983" viewBox="0 0 656 983" aria-label="The Voice of the Lord">
    <text x="38" y="269" textLength="582" lengthAdjust="spacingAndGlyphs"
          font-family="Bebas Neue, sans-serif" font-size="152" fill="#f7931e">THE VOICE OF</text>
    <text x="37" y="429" textLength="581" lengthAdjust="spacingAndGlyphs"
          font-family="Bebas Neue, sans-serif" font-size="210" fill="#f7f8fa">THE LORD</text>
  </svg>

  <div class="brand">SOLARA</div>
  <div class="edition">LUMEN 2025</div>
  <div class="subtitle">A PROPHETIC CONFERENCE</div>

  <section class="dates">
    <div class="date-card">
      <div class="date-month">DECEMBER</div>
      <div class="date-day">26</div>
      <div class="date-weekday">FRIDAY</div>
      <div class="date-time">6:30PM - 9:00PM</div>
    </div>
    <div class="date-card">
      <div class="date-month">DECEMBER</div>
      <div class="date-day">27</div>
      <div class="date-weekday long">SATURDAY</div>
      <div class="date-time">5:30PM - 8:00PM</div>
    </div>
    <div class="date-card">
      <div class="date-month">DECEMBER</div>
      <div class="date-day">28</div>
      <div class="date-weekday">SUNDAY</div>
      <div class="date-time">4:30PM - 7:00PM</div>
    </div>
  </section>

  <section class="location">
    <h2 class="location-title">LOCATION</h2>
    <p class="location-address">The Harborview Performing Arts Center<br>128 Linden Avenue<br>Millbrook, Maine 04000</p>
  </section>

  <section class="app-promo">
    <div class="app-screen">
      <div class="app-brand">SOLARA</div>
      <div class="app-call">DOWNLOAD THE</div>
      <div class="app-name">SOLARA APP</div>
      <div class="app-note">to stay updated on the event</div>
      <div class="store-badges">
        <span class="store-badge"></span>
        <span class="store-badge"></span>
      </div>
    </div>
  </section>

  <div class="speaker">
    <div class="speaker-label">SPEAKER</div>
    <div class="speaker-name">Prophet Samuel Okoro</div>
  </div>

  <footer class="contact-bar">
    <div class="contact-item contact-phone">
      <svg viewBox="0 0 24 24" fill="none" stroke="#fff" stroke-width="2"><path d="M5 3h4l2 5-2.5 1.5a11 11 0 0 0 6 6L16 13l5 2v4a2 2 0 0 1-2 2A16 16 0 0 1 3 5a2 2 0 0 1 2-2z"/></svg>
      <span class="divider"></span>207 555 0142
    </div>
    <div class="contact-item contact-mail">
      <svg viewBox="0 0 24 24" fill="none" stroke="#fff" stroke-width="2"><rect x="2" y="5" width="20" height="14"/><path d="M2 5l10 8 10-8"/></svg>
      <span class="divider"></span>contact@solara.org
    </div>
    <div class="contact-item contact-web">
      <svg viewBox="0 0 24 24" fill="none" stroke="#fff" stroke-width="2"><circle cx="12" cy="12" r="10"/><ellipse cx="12" cy="12" rx="4" ry="10"/><path d="M2 12h20M4 7h16M4 17h16"/></svg>
      <span class="divider"></span>www.solara.org
    </div>
  </footer>
</main>
</body>
</html>
```